'Little Lantern' promotional brochure

We have designed a 6 week program to educate impending first-time parents about the things they need to know to survive the first 6 months. Sessions delivered by general practitioner/family doctor, dietician, physiotherapist, speech pathologist and psychologist. Our promotional blurb is: 'A comprehensive education program for first-time parents-to-be, delivered over 6 weeks by health professionals in your community, about everything you need to know to look after your baby (and yourself!) in the first 6 months'. I now want to put together a promotional brochure to be distributed to those couples who express an interest which will provide further details of what will be delivered in the course.
Updates
In terms of layout, I envisaged a double sided A4 size, foldable into 3 sections, but very happy to be guided on this.
Target Market(s)
To appeal to a young, well educated demographic. First time parents couples.
Industry/Entity Type
Medical
Font styles to use
Other font styles liked:
- Playfair Display
Requirements
Must have
- Playfair display font to be consistent with our logo (attached). Logo also included please. Some consistency with colours of logo please.
Nice to have
- I am a doctor, and have no creative genes! But prefer a clean and professional appearance overall. Not too cluttered in overall appearance.
Should not have
- No cheesy pictures of babies.

```html
<!DOCTYPE html>
<html lang="en">
<head>
<meta charset="utf-8">
<title>Little Lantern – Our Weekly Programme</title>
<link rel="stylesheet" href="https://fonts.googleapis.com/css2?family=Playfair+Display:wght@400;700&display=swap">
<style>
  :root {
    --lime: #9dcb3c;
    --ink: #1c1c1c;
    --text: #2e2e2e;
    --paper: #ffffff;
    --photo-a: #c9c3b8;
    --photo-b: #8f8a80;
  }
  * { box-sizing: border-box; margin: 0; padding: 0; }
  html, body { width: 1200px; height: 848px; overflow: hidden; background: var(--paper); }
  .panel {
    position: relative; width: 1200px; height: 848px; overflow: hidden;
    font-family: "Playfair Display", Georgia, serif; color: var(--text);
    font-size: 17.5px; line-height: 22.1px;
  }
  .frame-bands { position: absolute; inset: 0; }
  .abs { position: absolute; white-space: nowrap; }
  .title-tab {
    left: 0; top: 0; width: 373px; height: 64px; background: var(--ink);
    border-bottom-right-radius: 34px; color: var(--lime);
    font-size: 28px; line-height: 64px; padding-left: 17px; font-weight: 400;
  }
  .week-pill {
    width: 153px; height: 50px; background: var(--lime); color: #fff;
    border-radius: 25px; font-size: 33px; line-height: 50px; text-align: center;
  }
  .name-tag {
    background: var(--ink); color: var(--lime); border-radius: 30px 0 0 30px;
    font-size: 21px; line-height: 1.05; display: flex; align-items: center; padding-left: 20px;
  }
  .portrait {
    border: 5px solid var(--lime);
    border-radius: 4px 26px 4px 26px;
    background: linear-gradient(160deg, var(--photo-a), var(--photo-b));
  }
  .session-head { font-weight: 700; font-size: 22px; line-height: 26px; color: var(--ink); }
  .hl { color: var(--lime); }
  .topic-list { list-style: none; font-size: 15.5px; }
  .topic-list li { position: relative; padding-left: 18px; }
  .topic-list li::before {
    content: ""; position: absolute; left: 0; top: 9px; width: 8px; height: 8px;
    border-radius: 50%; background: var(--lime);
  }
  .list-mum { line-height: 26px; }
  .list-mum li::before { top: 9px; }
  .list-baby { line-height: 25.4px; }
  .wrap-line { display: block; line-height: 21px; }
</style>
</head>
<body>
<main class="panel">
  <svg class="frame-bands" width="1200" height="848" viewBox="0 0 1200 848" aria-hidden="true">
    <path d="M581 0 H1200 V24 H605 Q581 24 581 0 Z" fill="var(--lime)"/>
    <path d="M1177 0 H1200 V770 Q1177 770 1177 746 Z" fill="var(--lime)"/>
    <path d="M0 214 Q26 214 26 240 V848 H0 Z" fill="var(--lime)"/>
    <path d="M0 824 H755 Q777 824 777 848 H0 Z" fill="var(--lime)"/>
  </svg>

  <h1 class="abs title-tab">Our Weekly Programme</h1>

  <!-- Column one -->
  <div class="abs portrait" style="left:192px; top:88px; width:177px; height:191px" role="img" aria-label="Portrait photo of GP Dr Helen Marsh"></div>
  <div class="abs week-pill" style="left:31px; top:141px">Week 1</div>
  <div class="abs name-tag" style="left:37px; top:212px; width:155px; height:64px">Dr Helen<br>Marsh</div>
  <p class="abs" style="left:28px; top:292px">GP <span class="hl">Dr Helen Marsh</span> will share<br>information for Mum's own health<br>after delivery. Topics include:</p>
  <ul class="abs topic-list list-mum" style="left:40px; top:366px">
    <li>Vaccinations in pregnancy</li>
    <li>Bleeding, bladder and bowel after delivery</li>
    <li>Breastfeeding, engorgement and mastitis</li>
    <li>Bottle feeding</li>
    <li>Post-natal anxiety &amp; depression</li>
    <li>Intimacy and contraception</li>
  </ul>
  <div class="abs week-pill" style="left:31px; top:567px">Week 2</div>
  <h2 class="abs session-head" style="left:28px; top:644px">Session 1</h2>
  <p class="abs" style="left:28px; top:674px">Clinical Psychologist <span class="hl">Dr Nina Hollis</span><br>will discuss changes in relationships as<br>couples becomes parents, gender roles<br>in parenting and post-natal depression.</p>

  <!-- Column two -->
  <h2 class="abs session-head" style="left:428px; top:21px">Session 2</h2>
  <p class="abs" style="left:428px; top:53px">Physiotherapist <span class="hl">Tara Wells</span> will present<br>advice for Mums regarding exercise during<br>and after pregnancy, looking after the pelvic<br>floor during and after pregnancy, and<br>abdominal muscle separation management.<br>She will also provide advice for promoting<br>babies' neck strength<br>and minimising the<br>risk of flat spots on<br>the head and<br>encouraging<br>gross motor skills in<br>the first 6 months</p>
  <div class="abs portrait" style="left:593px; top:221px; width:195px; height:189px" role="img" aria-label="Portrait photo of physiotherapist Tara Wells"></div>
  <div class="abs name-tag" style="left:422px; top:346px; width:171px; height:57px">Tara Wells</div>

  <div class="abs portrait" style="left:593px; top:439px; width:174px; height:191px" role="img" aria-label="Portrait photo of dietician Amy Calder"></div>
  <div class="abs week-pill" style="left:423px; top:472px">Week 3</div>
  <h2 class="abs session-head" style="left:436px; top:530px">Session 1</h2>
  <div class="abs name-tag" style="left:435px; top:563px; width:158px; height:57px">Amy Calder</div>
  <p class="abs" style="left:428px; top:640px">Dietician <span class="hl">Amy Calder</span> provides advice for<br>Mums regarding healthy eating during<br>pregnancy and lactation, normal weight<br>gain during pregnancy and realistic<br>weight loss after. She will also discuss the<br>evidence regarding breastfeeding VS<br>bottle-feeding, normal infant weight gain<br>and introducing solids (including those</p>

  <!-- Column three -->
  <p class="abs" style="left:825px; top:32px">with potential for allergy).</p>
  <h2 class="abs session-head" style="left:825px; top:74px">Session 2</h2>
  <p class="abs" style="left:825px; top:111px">Paediatric Speech Pathologist <span class="hl">Ruth Ellery</span><br>will share information about latching and<br>breast-feeding troubles &amp; tongue tie,<br>advice about dummies and<br>finger-sucking, introducing solids &amp;<br>feeding (including ‘pouch’ food),<br>encouraging language development and<br>current evidence<br>about electronic<br>devices impacting<br>language<br>development.</p>
  <div class="abs portrait" style="left:988px; top:288px; width:173px; height:191px" role="img" aria-label="Portrait photo of speech pathologist Ruth Ellery"></div>
  <div class="abs name-tag" style="left:824px; top:409px; width:164px; height:57px">Ruth Ellery</div>

  <div class="abs week-pill" style="left:835px; top:531px">Week 4</div>
  <p class="abs" style="left:825px; top:597px">GP <span class="hl">Dr Helen Marsh</span> will share advice<br>about your babies' health in the first<br>6 months, including:</p>
  <ul class="abs topic-list list-baby" style="left:830px; top:675px">
    <li>Skin of newborns</li>
    <li>Sleeping</li>
    <li>Crying</li>
    <li>Immunisations</li>
    <li>Fever and infections</li>
    <li>Diarrhoea and constipation</li>
  </ul>
  <ul class="abs topic-list list-baby" style="left:1016px; top:675px">
    <li>Teething</li>
    <li>Understanding a<span class="wrap-line">baby's signals</span></li>
  </ul>
</main>
</body>
</html>
```